A unique communication angle to crowdfunding

Looking for a fresh redesign of a crowd funding website that deals in real estate. I already have the content, but am looking to take the design to the next level.

Existing real estate crowd funding sites focus on the real estate. I want to explore communication angle that:
- puts the investor in the centre of the communication: "become a baron"
- highlights the international nature (international properties, international investors)

There's also quite a lot of copy on the site, as we need to explain the service in quite a bit of detail. There's room to reduce the copy and replace with graphics. Could also consider clicking to see different text (see our difference section in http://galleonfairs.com)

The backend of the platform is already being worked on by a specialist crowd funding service provider.

In total there are 5 pages to be designed.

The homepage is really important. Right now it looks quite dated. It doesn't have a great layout. Note there is no mobile version of the website, so the pages need to be seen well on mobile devices. When looking at the brief, refer to the following links too:

current website:
http://pennyduke.com

some revisions made so far:
http://preview.stakeharbor.com/7K3LQ9

Attached are logo files and another file which contained copy for the pages. No need to rework the logo.

Please make sure to use the same copy in the brief on the webpages, to ensure the layouts work. Designers are free to propose images they feel work on the pages.

I would like to see if rather than tweaking the pages, it's possible to come up with a better design concept. If the 5 pages are accepted, there's a chance I'll request an additional 4 pages.
Updates

Please note the font used in the logo is called "harabara" in case you decide to use it in any of the titles, etc.

Please note there is one additional page for which we would like to review designs. Note the page would be a template to be used on all future real estate detail pages. Here is an example of the current design for reference:

http://pennyduke.com/projects/view/14

In total there are 5 page designs required, (homepage + 4)

Thank you

FYI -

Just a quick note to give information from similar UK real estate crowdfunding sites:
http://www.housewalrus.co.uk
http://tiderock.co.uk
https://www.fundquarry.com

Of the above, only tiderock has a nice clean looking landing page. Information is clear and well laid out.

Hi all, just uploaded a new file in the brief. Contains some comments and a website reference. I thought it may help to explain how we could convey international aspect as well as how we could convey images in a more modern way. This is an option you can consider, but its entirely up to you how how answer the brief. Thanks!

Reason: As requested by some designers needing more time to complete their work. Continue to share your work in progress and receive timely feedback before the deadline.

We would like to let you know that we have just shortlisted the best designs. Together with that, we have also passed some detailed feedback to all designers who weren't shortlisted. If we didn't contact you, please let us know. If you haven't submitted a design or are working on revisions, please note these will no longer be taken into account now. We hope you understand that we need to close the project today. Thank you all once again for your great work and design concepts. Here's hoping we meet again on a future design brief. Cheers, pennyduke team.

Target Market(s)

At the moment, only rich are able to buy real estate. With this service, anyone can become a landlord. Target buyers:

Young professionals, looking to diversify from stock market and lower risk
People nearing retirement, looking for stable rental incomes
Retirees - looking to supplement pensions with possibility of capital gains
Parents - looking for a way to save long term for their children (instead of low interest paying bank accounts)

Industry/Entity Type

Communication

Font styles to use
Sans Serif
Other font styles liked:
• harabara

Colors
add136
f5f9eb
959595
000000

Requirements
Must have
• Overall, the site must convey "whoever you are, you too can become a landlord", and that you don't need to be wealthy to invest in real estate. See

Communication should put the investor (or the baron) at the centre. The investor can be any of those described in the target market.

Show the aspirational side of property ownership.

In addition to the investor/baron character, the second main theme is international. No other real estate crowdfunding website highlights this.
Nice to have
• Banner could show different consumer types, to illustrate that the service can appeal to many different profiles. Refer to attached file "home page reference - plainasbread.com" as an example of how this could be done.

Aim to show the international side of the service. Properties around the world, investors around the world.

```html
<!DOCTYPE html>
<html lang="en">
<head>
<meta charset="utf-8">
<title>pennyduke – Become a property baron</title>
<link rel="stylesheet" href="https://fonts.googleapis.com/css2?family=Open+Sans:wght@400;600;700&family=Raleway:wght@300;400;600;700&display=swap">
<style>
:root{
  --green:#add136;
  --green-dark:#8fb01f;
  --pale:#f5f9eb;
  --grey:#959595;
  --grey-light:#e6e6e6;
  --black:#000;
  --pink:#e23a6a;
  --white:#fff;
  --text:#555;
}
*{box-sizing:border-box;margin:0;padding:0}
html,body{width:1200px;height:4000px;overflow:hidden;background:var(--white)}
body{font-family:"Open Sans",Arial,sans-serif;color:var(--text);position:relative}
.section{position:relative;width:1200px;overflow:hidden}

/* hero */
.hero{height:900px}
.hero-photo{position:absolute;inset:0;background:linear-gradient(180deg,#3c5468 0%,#5a7284 35%,#27394a 58%,#1b2a36 70%,#3a5060 82%,#141f28 100%)}
.site-header{position:absolute;top:0;left:0;right:0;height:80px;background:rgba(0,0,0,.35);display:flex;align-items:center;padding:0 30px}
.brand{display:flex;align-items:center;gap:12px;font-family:"Raleway",sans-serif;font-weight:700;font-size:30px;color:var(--green)}
.brand-dot{width:34px;height:34px;border-radius:50%;background:var(--green)}
.main-nav{display:flex;gap:26px;margin-left:60px}
.main-nav a{font-family:"Raleway",sans-serif;font-size:15px;font-weight:600;color:var(--white);text-decoration:none;letter-spacing:.5px}
.social{display:flex;gap:12px;margin-left:auto}
.social span{width:30px;height:30px;border-radius:50%;border:2px solid var(--white)}
.hero-title{position:absolute;top:470px;left:0;right:0;text-align:center;color:var(--white);font-family:"Raleway",sans-serif;text-transform:uppercase}
.hero-title .lead{display:block;font-size:36px;font-weight:300;letter-spacing:4px}
.hero-title .strong{display:block;font-size:38px;font-weight:700;letter-spacing:1px;margin-top:4px}
.hero-next{position:absolute;top:625px;left:545px}
.hero-dots{position:absolute;top:852px;left:0;right:0;display:flex;justify-content:center;gap:14px}
.hero-dots span{width:14px;height:14px;border-radius:50%;background:rgba(255,255,255,.5)}
.hero-dots span.on{background:var(--white)}

/* intro */
.intro{height:265px;background:var(--green);text-align:center;color:var(--white)}
.intro-icon{margin:22px auto 0;display:block}
.intro h2{font-family:"Raleway",sans-serif;font-size:27px;font-weight:700;margin-top:12px}
.intro p{font-size:19px;line-height:26px;width:860px;margin:10px auto 0}

/* paths */
.paths{height:235px;background:var(--pale);display:flex;justify-content:center;gap:80px;padding-top:55px}
.path{display:flex;gap:24px;width:420px}
.path-button{width:110px;height:110px;background:var(--grey);color:var(--white);display:flex;flex-direction:column;align-items:center;justify-content:flex-end;padding-bottom:12px;text-align:center;font-size:12px;line-height:15px;text-transform:uppercase;flex-shrink:0}
.path-button svg{margin-bottom:12px}
.path h3{font-family:"Raleway",sans-serif;font-size:30px;font-weight:600;color:#444}
.path p{font-size:18px;line-height:24px;color:var(--grey);margin-top:4px}

/* featured */
.featured{height:665px;text-align:center}
.section-title{font-family:"Raleway",sans-serif;font-size:30px;font-weight:700;color:var(--green)}
.featured .section-title{margin-top:30px}
.section-sub{font-size:19px;line-height:26px;color:var(--grey);width:820px;margin:6px auto 0}
.section-sub a{color:var(--green);text-decoration:none}
.project-list{display:flex;justify-content:center;gap:26px;margin-top:35px;text-align:left}
.project{width:330px;border:1px solid #ddd;background:var(--white);box-shadow:0 2px 6px rgba(0,0,0,.1);height:440px}
.project-photo{height:160px;position:relative}
.project-photo .ph{position:absolute;inset:0}
.price-tag{position:absolute;top:0;right:0;background:var(--green);color:var(--white);font-weight:700;font-size:15px;padding:8px 14px}
.new-badge{position:absolute;top:14px;left:14px;background:#2d6fb6;color:var(--white);font-size:11px;padding:3px 10px}
.project-body{padding:16px 18px}
.project h4{font-size:16px;color:#333;font-weight:700}
.project p{font-size:13px;line-height:18px;color:var(--grey);margin-top:6px;height:90px}
.bar{height:10px;background:var(--grey-light);margin-top:12px}
.bar i{display:block;height:100%;background:var(--green)}
.funded{font-size:14px;color:var(--grey);margin-top:8px}
.project-link{display:block;border-top:1px solid #eee;margin-top:14px;padding-top:10px;font-size:14px;color:var(--green-dark);text-decoration:none;font-weight:600}

/* community */
.community{height:665px;text-align:center}
.band-label{width:960px;height:40px;margin:28px auto 0;background:var(--green);color:var(--white);font-size:18px;line-height:40px}
.world-map{width:980px;height:360px;margin:20px auto 0;background:linear-gradient(180deg,#c9c9c9,#b5b5b5);border-radius:6px}
.legend{width:960px;margin:22px auto 0;text-align:left}
.legend div{display:flex;align-items:center;gap:14px;font-size:17px;color:var(--grey);margin-bottom:10px}
.legend i{width:24px;height:24px;display:block}

/* buying power */
.power{height:635px}
.power .band-label{margin-top:30px}
.donut{position:absolute;left:255px;top:100px}
.donut-label{position:absolute;left:765px;font-size:22px;color:#444}
.donut-note{position:absolute;left:230px;top:520px;width:520px;font-size:16px;line-height:22px;color:var(--grey)}

/* press */
.press{height:150px;border-top:1px solid #ddd;padding:20px 60px}
.press h5{font-size:13px;color:var(--grey);font-weight:400}
.press-row{display:flex;gap:28px;margin-top:12px;flex-wrap:wrap;width:1080px}
.press-row span{height:34px;background:#c8c8c8;border-radius:4px}

/* footer */
.site-footer{position:absolute;top:3515px;left:0;width:1200px;height:485px;background:var(--black);color:#bbb;padding:34px 60px 0}
.footer-top{display:flex;justify-content:space-between;align-items:flex-start}
.footer-top p{width:760px;font-size:15px;line-height:22px}
.group-name{font-size:30px;font-weight:700;color:var(--white)}
.legal{font-size:12px;line-height:18px;color:#999;margin-top:40px}
.legal + .legal{margin-top:14px}
.footer-bar{position:absolute;left:0;right:0;bottom:0;height:70px;border-top:1px solid #333;display:flex;justify-content:center;align-items:center;gap:12px;color:#ccc;font-size:17px}
.footer-bar span.c{width:28px;height:28px;border-radius:50%;border:2px solid #ccc;display:inline-block}
</style>
</head>
<body>

<section class="section hero">
  <div class="hero-photo" role="img" aria-label="City waterfront at dusk with high-rise towers reflected in the water"></div>
  <header class="site-header">
    <div class="brand"><span class="brand-dot"></span>pennyduke</div>
    <nav class="main-nav">
      <a href="#">HOME</a><a href="#">SIGN IN</a><a href="#">HOW IT WORKS</a><a href="#">DISCOVER A PROJECT</a><a href="#">THE BARON BLOG</a><a href="#">FIND OUT MORE</a>
    </nav>
    <div class="social"><span></span><span></span></div>
  </header>
  <h1 class="hero-title"><span class="lead">Property buying</span><span class="strong">is stressful, outdated and in need of change.</span></h1>
  <svg class="hero-next" width="110" height="110" viewBox="0 0 110 110" aria-hidden="true">
    <circle cx="55" cy="55" r="50" fill="none" stroke="#fff" stroke-width="5"/>
    <polyline points="33,45 55,67 77,45" fill="none" stroke="#fff" stroke-width="7" stroke-linecap="round" stroke-linejoin="round"/>
  </svg>
  <div class="hero-dots"><span class="on"></span><span></span><span></span><span></span></div>
</section>

<section class="section intro">
  <svg class="intro-icon" width="80" height="80" viewBox="0 0 80 80" aria-hidden="true">
    <circle cx="40" cy="40" r="38" fill="#fff"/>
    <path d="M24 56 L48 32 M52 22 a8 8 0 1 0 6 6 l-6 2 z" stroke="#add136" stroke-width="6" fill="none" stroke-linecap="round"/>
    <path d="M26 26 L54 54" stroke="#add136" stroke-width="6" stroke-linecap="round"/>
  </svg>
  <h2>Reconstructing a property ladder that's strong and fair</h2>
  <p>By harnessing the power of crowds, it's possible to become a landlord in locations around the world. Forget the burden of financing 100% of the purchase. Leave the day to day management of your property portfolio to us. Start with 1% in a project and plan your steps to becoming a true baron.</p>
</section>

<section class="section paths">
  <div class="path">
    <div class="path-button">
      <svg width="40" height="40" viewBox="0 0 40 40" aria-hidden="true"><polyline points="14,6 28,20 14,34" fill="none" stroke="#fff" stroke-width="4"/></svg>
      Sign up<br>to buy
    </div>
    <div><h3>Find properties</h3><p>Sign up to browse the portfolio. Your journey to becoming a real estate baron starts here.</p></div>
  </div>
  <div class="path">
    <div class="path-button">
      <svg width="40" height="40" viewBox="0 0 40 40" aria-hidden="true"><polyline points="14,6 28,20 14,34" fill="none" stroke="#fff" stroke-width="4"/></svg>
      Submit<br>a property
    </div>
    <div><h3>Find buyer</h3><p>Submit a property or development and raise funds from our real estate barons.</p></div>
  </div>
</section>

<section class="section featured">
  <h2 class="section-title">Featured Projects</h2>
  <p class="section-sub">Brief details of new and popular projects. To view full listings, you will be required to sign up and <a href="#">become a member.</a></p>
  <div class="project-list">
    <article class="project">
      <div class="project-photo">
        <div class="ph" role="img" aria-label="Riverside apartment building" style="background:linear-gradient(180deg,#8aa3b8,#4a5d6c)"></div>
        <span class="new-badge">new launch</span><span class="price-tag">From GBP 5,600</span>
      </div>
      <div class="project-body">
        <h4>21 Harbour Lane LONDON E1</h4>
        <p>A landmark development in E1 offering panoramic views across the river Thames less than 2 miles from the City and the docks.</p>
        <div class="bar"><i style="width:0"></i></div>
        <div class="funded">0% funded</div>
        <a class="project-link" href="#">See Project Details</a>
      </div>
    </article>
    <article class="project">
      <div class="project-photo">
        <div class="ph" role="img" aria-label="Waterside residential tower at night" style="background:linear-gradient(180deg,#3e5a7a,#1c2b3c)"></div>
        <span class="new-badge">new launch</span><span class="price-tag">From GBP 3,275</span>
      </div>
      <div class="project-body">
        <h4>Meridian Tower, LONDON E14</h4>
        <p>At the heart of Old Quay Wharf, a premium residential project by award winning developer Stonefield.</p>
        <div class="bar"><i style="width:4%"></i></div>
        <div class="funded">4% funded</div>
        <a class="project-link" href="#">See Project Details</a>
      </div>
    </article>
    <article class="project">
      <div class="project-photo">
        <div class="ph" role="img" aria-label="Colourful island apartment blocks by the water" style="background:linear-gradient(180deg,#a8bfd0,#6d7f8c)"></div>
        <span class="new-badge">new launch</span><span class="price-tag">From GBP 760</span>
      </div>
      <div class="project-body">
        <h4>Canal Point Island E14</h4>
        <p>A new island for London, introducing the most connected location from the multi-award winning developer, Stonefield Group.</p>
        <div class="bar"><i style="width:51%"></i></div>
        <div class="funded">51% funded</div>
        <a class="project-link" href="#">See Project Details</a>
      </div>
    </article>
  </div>
</section>

<section class="section community">
  <h2 class="section-title">Be Part of a Growing International Community</h2>
  <p class="section-sub">Gain access to new projects in world class cities and join our growing community of international landlords.</p>
  <div class="band-label">A community of international property &amp; real estate in the maps</div>
  <div class="world-map" role="img" aria-label="World map marking property barons and real estate locations around the globe"></div>
  <div class="legend">
    <div><i style="background:var(--green)"></i>A community of international property barons</div>
    <div><i style="background:var(--pink)"></i>Attractive real estate from around the world</div>
  </div>
</section>

<section class="section power">
  <div class="band-label">Collective buying power of the pennyduke community</div>
  <svg class="donut" width="400" height="400" viewBox="0 0 400 400" role="img" aria-label="Donut chart: invested 15.8%, pledged 84.2%">
    <circle cx="200" cy="200" r="150" fill="none" stroke="#add136" stroke-width="70"/>
    <circle cx="200" cy="200" r="150" fill="none" stroke="#959595" stroke-width="70" stroke-dasharray="148.9 1000" transform="rotate(-90 200 200)"/>
    <text x="200" y="190" text-anchor="middle" font-family="Open Sans, sans-serif" font-size="38" fill="#add136">* USD</text>
    <text x="200" y="240" text-anchor="middle" font-family="Open Sans, sans-serif" font-size="46" font-weight="700" fill="#add136">$2.06m</text>
  </svg>
  <div class="donut-label" style="top:130px">Invested 15.8%</div>
  <div class="donut-label" style="top:335px">Pledged 84.2%</div>
  <p class="donut-note">* Graphic shows the combined USD$ amount invested in projects and pledged from aspiring pennydukes</p>
</section>

<section class="section press">
  <h5>Featured in</h5>
  <div class="press-row">
    <span style="width:110px"></span><span style="width:110px"></span><span style="width:130px"></span><span style="width:90px"></span><span style="width:50px"></span><span style="width:130px"></span>
    <span style="width:50px"></span><span style="width:90px"></span><span style="width:330px"></span>
  </div>
</section>

<footer class="site-footer">
  <div class="footer-top">
    <p>Pennyduke is part of the Rootfund Group. The Rootfund Group is a worldwide pioneer and leader in the crowd investing, peer to peer and online investment market.</p>
    <div class="group-name">Rootfund Group</div>
  </div>
  <p class="legal">By accessing this site and any pages thereof, you agree to be bound by the terms and conditions. This website is only suitable, intended and available for professional or sophisticated investors in certain jurisdictions, or those who are members of the pennyduke community and familiar with the risks of private investment. Pennyduke does not endorse any of the projects that appear on this website, nor does it make any recommendation regarding the suitability of particular opportunities for any participant. Each potential participant must review and evaluate the projects in his or her own discretion and determine the suitability of participating.</p>
  <p class="legal">This website (the "Site") is in no way affiliated with any site to which it links or with any company or entity named in listed projects. Pennyduke has no commercial relationship with such third parties and accepts no liability for their content. Any content used on this Site is referenced with permission. If you believe your content has been reproduced without consent, please refer to our Terms of Service for information on how to request its removal from the Site.</p>
  <div class="footer-bar">© pennyduke 2014 | Follow pennyduke <span class="c"></span><span class="c"></span></div>
</footer>

</body>
</html>
```